BrimFalcon Business Cards

We have a defined brand. Please visit our website to get a feel for the product and the color pallets. www.brimfalcon-example.com

We need an updated, world class business card design. (See the attached existing card design). Please utilize BOTH sides of the card as shown and be creative with the layout. I do want the horse head icon to be positioned as it is with the existing card.

The remainder of the layout can be customized and I also want it vertically oriented.

Attached are the logo files and please use the colors as follows:
Green - #A5CE39
Tan - #CDBD99
Black

Feel free to play with the colors.

```html
<!DOCTYPE html>
<html lang="en">
<head>
<meta charset="utf-8">
<title>BrimFalcon Business Cards</title>
<link href="https://fonts.googleapis.com/css2?family=Michroma&family=Open+Sans:wght@400;600&display=swap" rel="stylesheet">
<style>
  :root {
    --stage: #ecebe8;
    --paper: #ffffff;
    --ink: #111111;
    --green-deep: #3f8f45;
    --green-mid: #7ab534;
    --green-bright: #c5d72a;
    --icon-green: #a5c93a;
    --tan: #cdbd99;
    --shadow: rgba(0,0,0,0.22);
  }
  * { box-sizing: border-box; margin: 0; padding: 0; }
  html, body { width: 1200px; height: 900px; overflow: hidden; }
  body { background: var(--stage); position: relative; font-family: "Open Sans", sans-serif; color: var(--ink); }

  .card { position: absolute; top: 187px; width: 300px; height: 525px; box-shadow: 0 8px 22px var(--shadow); overflow: hidden; }

  .mark-dot { display: block; border-radius: 50%; background: var(--ink); flex: none; }
  .brand-name { font-family: "Michroma", sans-serif; line-height: 1; color: var(--ink); white-space: nowrap; }
  .tagline { font-weight: 600; color: #1f2a10; white-space: nowrap; }

  /* Back: white with centred mark */
  .card-back { left: 90px; background: var(--paper);
    display: flex; flex-direction: column; align-items: center; justify-content: center; gap: 22px; }
  .card-back .mark-dot { width: 72px; height: 72px; }
  .card-back .brand-name { font-size: 26px; }
  .card-back .tan-rule { width: 60px; height: 3px; background: var(--tan); }

  /* Front: green field with stacked lockup */
  .card-front { left: 450px;
    background: radial-gradient(ellipse at 50% 52%, var(--green-bright) 0%, var(--green-mid) 45%, var(--green-deep) 100%);
    display: flex; flex-direction: column; align-items: center; justify-content: center; text-align: center; }
  .card-front .mark-dot { width: 58px; height: 58px; margin-bottom: 18px; }
  .card-front .brand-name { font-size: 26px; }
  .card-front .tagline { font-size: 12px; letter-spacing: 2px; margin-top: 10px; }

  /* Contact side */
  .card-contact { left: 810px; background: var(--paper); }
  .card-contact .swoosh { position: absolute; inset: 0; width: 100%; height: 100%; }
  .contact-lockup { position: absolute; left: 24px; top: 36px; display: flex; align-items: center; gap: 10px; }
  .contact-lockup .mark-dot { width: 34px; height: 34px; }
  .contact-lockup .brand-name { font-size: 19px; }
  .contact-lockup .tagline { font-size: 10px; letter-spacing: 1.6px; margin-top: 5px; }

  .person { position: absolute; left: 24px; top: 128px; }
  .person .name { font-family: "Michroma", sans-serif; font-size: 15px; letter-spacing: 3px; }
  .person .role { font-size: 11px; margin-top: 3px; }
  .person .tan-rule { width: 44px; height: 3px; background: var(--tan); margin-top: 10px; }

  .details { position: absolute; left: 24px; top: 212px; list-style: none; font-size: 13px; line-height: 1.45; }
  .details li { display: flex; align-items: flex-start; gap: 10px; margin-bottom: 3px; }
  .details svg { width: 15px; height: 15px; flex: none; margin-top: 2px; fill: var(--icon-green); }
  .details .address { margin-top: 10px; }
</style>
</head>
<body>

<section class="card card-back" aria-label="Card back">
  <span class="mark-dot"></span>
  <span class="brand-name">BrimFalcon</span>
  <span class="tan-rule"></span>
</section>

<section class="card card-front" aria-label="Card front">
  <span class="mark-dot"></span>
  <div class="brand-name">BrimFalcon</div>
  <div class="tagline">Performance Driven EVs</div>
</section>

<section class="card card-contact" aria-label="Contact card">
  <svg class="swoosh" viewBox="0 0 300 525" preserveAspectRatio="none">
    <defs>
      <radialGradient id="swoosh-fill" cx="0.65" cy="0.85" r="0.7">
        <stop offset="0" stop-color="#c5d72a"/>
        <stop offset="0.5" stop-color="#7ab534"/>
        <stop offset="1" stop-color="#3f8f45"/>
      </radialGradient>
    </defs>
    <path d="M0,525 L0,500 C110,496 210,462 300,402 L300,525 Z" fill="url(#swoosh-fill)"/>
    <path d="M0,478 C110,482 200,450 275,398 C205,460 110,492 0,490 Z" fill="#111"/>
    <path d="M0,494 C110,496 205,464 290,404" fill="none" stroke="#cdbd99" stroke-width="2"/>
  </svg>

  <div class="contact-lockup">
    <span class="mark-dot"></span>
    <div>
      <div class="brand-name">BrimFalcon</div>
      <div class="tagline">Performance Driven EVs</div>
    </div>
  </div>

  <div class="person">
    <div class="name">DANIEL REYES</div>
    <div class="role">CEO/Managing Director</div>
    <div class="tan-rule"></div>
  </div>

  <ul class="details">
    <li><svg viewBox="0 0 24 24"><path d="M6.6 10.8a15 15 0 0 0 6.6 6.6l2.2-2.2c.3-.3.7-.4 1-.2 1.1.4 2.3.6 3.6.6.6 0 1 .4 1 1V20c0 .6-.4 1-1 1A17 17 0 0 1 3 4c0-.6.4-1 1-1h3.5c.6 0 1 .4 1 1 0 1.3.2 2.5.6 3.6.1.3 0 .7-.2 1z"/></svg>555-010-4477</li>
    <li><svg viewBox="0 0 24 24"><path d="M6 2h12v5H6zM4 8h16a2 2 0 0 1 2 2v6h-4v6H6v-6H2v-6a2 2 0 0 1 2-2zm4 8v4h8v-4z"/></svg>555-010-4478</li>
    <li><svg viewBox="0 0 24 24"><path d="M2 5h20v14H2zm2 2v.5l8 5.5 8-5.5V7z"/></svg>dreyes@brimfalcon-example.com</li>
    <li class="address"><svg viewBox="0 0 24 24"><path d="M12 2a7 7 0 0 0-7 7c0 5 7 13 7 13s7-8 7-13a7 7 0 0 0-7-7zm0 9.5A2.5 2.5 0 1 1 12 6.5a2.5 2.5 0 0 1 0 5z"/></svg>
      <span>418 Lindell Avenue NW<br>Suite 210, Cedar Point<br>MI 40010</span></li>
  </ul>
</section>

</body>
</html>
```